Web design for Crowdfunding site HopeWingsRally.com

We need a web design for christian crowdfunding website. Here is the challenge: We need responsive layout that is targeted first in iPad size of screen. It should also scale somehow down to iPhone size of screens. Web layout can be about the same size as iPad screen.

Screens should work so that main page scrolls not but only certain part of the screen scrolls and always one "page" at time. We can implement these "scrolls" then later with javascript but now we need only design. The challenge is to create this kind of hybrid website / app look.

Target is at first to raise funds to orphan people needing about $40 per month for their living and education. There is always some organization which takes care of these kids. Later there will be other christian missions included. At first we are looking to find monthly supporters.

You can be as creative as you want :) As you see from the look and feel sector, I am not looking any same traditional look which many "help kids" sites have. I am looking to reach now younger generation and therefore iPad and mobile are the main screen sizes.

Inspirational designs:
- https://example-gallery.test/profiles/studiofernlake/designs/482716?from=%2Fbrowse%2Fxhr%2Fdesigns%3Fcategory%3Dmobile-app-design
- http://www.artpoolhub.test/design/8261047 Clear, simple visuals
- http://www.artpoolhub.test/design/7394215 Header
- http://www.artpoolhub.test/design/6048392 Contrast in the colors, i think is powerfull

Some terms could be: Kids play, kids are learning (in the school). No static posture but living like kids are. I wonder also how we could also add little bit gaming style even though the question is of reali life of real people. Giving should be rewarding.

Target Market(s)

People who want help other people.

Industry/Entity Type

Christian

Number of Pages Required

4 page

Requirements
Must have
• Homepage. Mission page (In my wireframes it was one kid).
Nice to have
• Other pages and some idea how to scroll. 4 pages is no must. If you feel easy, please give first some draft and I give comments on that.

```html
<!DOCTYPE html>
<html lang="en">
<head>
<meta charset="utf-8">
<title>HopeWingsRally – Mission: Orphan Maria, 11y</title>
<link rel="stylesheet" href="https://fonts.googleapis.com/css2?family=Roboto:wght@300;400;500;700&display=swap">
<style>
  :root {
    --brand: #ffc107;
    --brand-deep: #f5b800;
    --white: #ffffff;
    --panel: #f6f7f9;
    --ink: #3c3c3c;
    --ink-soft: #6b6b6b;
    --ink-muted: #8a8a8a;
    --tab-dark: #5b5b5b;
    --rule: #e1e3e6;
    --ring-rest: #5e5e5e;
    --photo-a: #c9b7a6;
    --photo-b: #8a6f5c;
  }
  * { box-sizing: border-box; margin: 0; padding: 0; }
  html, body { width: 1200px; height: 900px; overflow: hidden; }
  body {
    position: relative;
    background: var(--white);
    font-family: "Roboto", Arial, sans-serif;
    color: var(--ink);
  }
  .abs { position: absolute; }

  /* Header */
  .site-header { left: 0; top: 0; width: 1200px; height: 87px; background: var(--brand); }
  .menu-toggle {
    left: 29px; top: 13px; width: 61px; height: 61px; border: 1.5px solid var(--white);
    border-radius: 50%; display: flex; align-items: center; justify-content: center;
  }
  .missions-link {
    left: 102px; top: 33px; color: var(--white); font-size: 15px; font-weight: 400;
    text-decoration: underline; text-underline-offset: 3px; display: flex; align-items: center; gap: 12px;
  }
  .brand-name {
    left: 0; width: 1200px; top: 24px; text-align: center; color: var(--white);
    font-size: 31px; font-weight: 500; letter-spacing: 0.3px;
  }
  .auth-btn {
    top: 21px; height: 45px; border: 1.5px solid var(--white); border-radius: 4px;
    color: var(--white); font-size: 18px; font-weight: 300;
    display: flex; align-items: center; justify-content: center; gap: 9px;
  }
  .auth-login { left: 920px; width: 122px; }
  .auth-signup { left: 1051px; width: 122px; }

  /* Panel */
  .mission-panel { left: 27px; top: 105px; width: 1146px; height: 770px; background: var(--panel); }

  .heading { font-size: 23px; font-weight: 500; color: var(--ink); }
  .heading .accent { color: var(--brand); }
  .mission-title { left: 27px; top: 129px; }

  .tab {
    top: 187px; height: 56px; border-radius: 3px; color: var(--white);
    font-size: 23px; font-weight: 500; display: flex; align-items: center; justify-content: center; gap: 12px;
    background: var(--tab-dark);
  }
  .tab.is-active { background: var(--brand); }
  .tab-story { left: 27px; width: 173px; }
  .tab-updates { left: 207px; width: 174px; }
  .tab-comments { left: 388px; width: 197px; }

  .timeline-line { left: 40px; top: 285px; width: 2px; height: 554px; background: var(--ink-muted); }
  .timeline-dot {
    left: 28px; width: 27px; height: 27px; border-radius: 50%; background: var(--ring-rest);
    display: flex; align-items: center; justify-content: center;
  }
  .timeline-dot.is-current { background: var(--brand); }

  .story-text { left: 81px; width: 680px; font-size: 16px; line-height: 31.6px; color: var(--ink-soft); font-weight: 400; }
  .photo {
    left: 81px; top: 469px; width: 677px; height: 230px;
    background: linear-gradient(100deg, var(--photo-a) 0%, var(--photo-b) 55%, #5d4a40 100%);
  }
  .copyright { left: 80px; top: 841px; font-size: 16px; color: var(--ink-soft); }

  /* Right column */
  .name-title { left: 793px; top: 129px; }
  .meta { left: 794px; font-size: 17px; color: var(--ink-soft); display: flex; align-items: center; gap: 8px; }
  .section-label { left: 792px; font-size: 20px; font-weight: 500; color: var(--ink-soft); }
  .rule { left: 792px; width: 380px; height: 1px; background: var(--rule); }
  .supporters { left: 1020px; top: 266px; display: flex; gap: 6px; }
  .supporter {
    width: 31px; height: 31px; border-radius: 50%; background: #e9e9e9; border: 1.5px solid var(--ink-muted);
    overflow: hidden; display: flex; align-items: flex-end; justify-content: center;
  }
  .support-now { left: 792px; top: 323px; font-size: 17px; color: var(--ink-muted); }

  .progress-ring { left: 792px; top: 373px; }
  .progress-value { left: 792px; top: 431px; width: 156px; text-align: center; font-size: 34px; font-weight: 400; color: var(--ink); }
  .given { left: 967px; top: 406px; font-size: 18px; font-weight: 700; color: var(--ink); }
  .needed { left: 967px; top: 437px; font-size: 18px; color: var(--ink-muted); }
  .per-month { left: 967px; top: 473px; font-size: 18px; font-weight: 700; color: var(--ink-soft); display: flex; align-items: center; gap: 12px; }

  .option {
    left: 803px; width: 359px; height: 44px; background: var(--white); border: 1px solid var(--rule);
    border-radius: 3px; display: flex; align-items: center; padding: 0 14px 0 14px; font-size: 17px; color: var(--ink-soft);
  }
  .option .box { width: 20px; height: 20px; border: 1px solid #c9c9c9; border-radius: 4px; background: #ececec; margin-right: 16px; flex: none; }
  .option .label { flex: 1; }
  .amount-field {
    width: 123px; height: 35px; border: 1px dashed #c9c9c9; border-radius: 3px; margin-right: 42px;
    font-size: 13px; color: var(--ink-muted); display: flex; align-items: center; padding-left: 11px;
  }
</style>
</head>
<body>

<header class="site-header abs">
  <div class="menu-toggle abs">
    <svg width="24" height="20" viewBox="0 0 24 20" fill="#fff" aria-hidden="true">
      <rect x="0" y="1" width="4" height="4" rx="1"/><rect x="7" y="1" width="17" height="4" rx="1"/>
      <rect x="0" y="8" width="4" height="4" rx="1"/><rect x="7" y="8" width="17" height="4" rx="1"/>
      <rect x="0" y="15" width="4" height="4" rx="1"/><rect x="7" y="15" width="17" height="4" rx="1"/>
    </svg>
  </div>
  <div class="missions-link abs">SEE THE MISSIONS
    <svg width="16" height="16" viewBox="0 0 16 16" fill="none" stroke="#fff" stroke-width="2.4" aria-hidden="true"><circle cx="6.5" cy="6.5" r="4.5"/><line x1="10" y1="10" x2="14.5" y2="14.5"/></svg>
  </div>
  <div class="brand-name abs">HOPEWINGSRALLY</div>
  <div class="auth-btn auth-login abs">
    <svg width="13" height="16" viewBox="0 0 13 16" fill="#fff" aria-hidden="true"><path d="M3 7V5a3.5 3.5 0 0 1 7 0v2h-2V5a1.5 1.5 0 0 0-3 0v2z"/><rect x="0.5" y="7" width="12" height="9" rx="1.5"/></svg>
    LOGIN
  </div>
  <div class="auth-btn auth-signup abs">
    <svg width="16" height="16" viewBox="0 0 16 16" fill="#fff" aria-hidden="true"><path d="M11 1.5l3.5 3.5L5.5 14H2v-3.5z"/></svg>
    SIGNUP
  </div>
</header>

<main class="mission-panel abs"></main>

<h1 class="heading mission-title abs">MISSION : <span class="accent">ORPHAN MARIA,11Y</span></h1>

<div class="tab tab-story is-active abs">
  <svg width="20" height="18" viewBox="0 0 20 18" fill="#fff" aria-hidden="true"><path d="M5 0h14l-4 15H1z"/><path d="M1 15h14l-.5 2H1.5a1 1 0 0 1 0-2z" opacity=".8"/></svg>
  STORY
</div>
<div class="tab tab-updates abs">
  <svg width="20" height="20" viewBox="0 0 20 20" fill="none" stroke="#fff" stroke-width="3" aria-hidden="true"><path d="M16 7a7 7 0 0 0-12.5-1"/><path d="M4 13a7 7 0 0 0 12.5 1"/><path d="M2 2v5h5" fill="#fff" stroke-width="0"/><path d="M18 18v-5h-5" fill="#fff" stroke-width="0"/></svg>
  UPDATES
</div>
<div class="tab tab-comments abs">
  <svg width="22" height="18" viewBox="0 0 22 18" fill="none" stroke="#fff" stroke-width="2" aria-hidden="true"><ellipse cx="9" cy="7" rx="8" ry="5.5"/><path d="M4 11l-2 4 5-2.5"/><path d="M17.5 8.5c2.5 1 3.5 3 2.5 5l1 3-3.5-1.5"/></svg>
  COMMENTS
</div>

<div class="timeline-line abs"></div>
<div class="timeline-dot abs" style="top:271px">
  <svg width="13" height="10" viewBox="0 0 13 10" fill="none" stroke="#fff" stroke-width="2.6" aria-hidden="true"><path d="M1.5 5l3.5 3.5 6.5-7"/></svg>
</div>
<div class="timeline-dot is-current abs" style="top:541px">
  <svg width="13" height="10" viewBox="0 0 13 10" fill="none" stroke="#fff" stroke-width="2.6" aria-hidden="true"><path d="M1.5 5l3.5 3.5 6.5-7"/></svg>
</div>
<div class="timeline-dot abs" style="top:825px">
  <svg width="13" height="10" viewBox="0 0 13 10" fill="none" stroke="#fff" stroke-width="2.6" aria-hidden="true"><path d="M1.5 5l3.5 3.5 6.5-7"/></svg>
</div>

<p class="story-text abs" style="top:271px">Sed ut perspiciatis unde omnis iste natus error sit voluptatem accusantium doloremque lau dan tium, totam rem aperiam, eaque ipsa quae ab illo inventore veritatis et quasi architecto magni dolores eos qui ratione voluptatem sequi nesciunt.</p>
<p class="story-text abs" style="top:383px">Sed ut perspiciatis unde omnis iste natus error sit voluptatem accusantium doloremque lau architecto&nbsp; magni dolores eos qui ratione voluptatem sequi nesciunt.</p>
<div class="photo abs" role="img" aria-label="Photo of young volunteers sorting donated toys and clothes in a charity shop"></div>
<p class="story-text abs" style="top:725px">Sed ut perspiciatis unde omnis iste natus error sit voluptatem accusantium doloremque lau dan tium, totam rem aperiam, eaque ipsa quae ab illo inventore veritatis et quasi architecto magni dolores eos qui ratione voluptatem sequi nesciunt.</p>
<div class="copyright abs">© Copyright 2016 Hopewingsrally.All Rights Reserved</div>

<!-- Mission summary -->
<h2 class="heading name-title abs">NAME : <span class="accent">MARIA,11Y</span></h2>
<div class="meta abs" style="top:177px">
  <svg width="10" height="14" viewBox="0 0 10 14" fill="#6b6b6b" aria-hidden="true"><path d="M5 0a5 5 0 0 1 5 5c0 3.5-5 9-5 9S0 8.5 0 5a5 5 0 0 1 5-5zm0 3a2 2 0 1 0 0 4 2 2 0 0 0 0-4z"/></svg>
  Kalkutta
</div>
<div class="meta abs" style="top:208px">Organization : ellis</div>

<div class="section-label abs" style="top:269px">Support</div>
<div class="supporters abs">
  <span class="supporter"><svg width="22" height="24" viewBox="0 0 22 24" fill="#9a9a9a" aria-hidden="true"><circle cx="11" cy="8" r="5.5"/><path d="M0 24c0-6 5-9 11-9s11 3 11 9z"/></svg></span>
  <span class="supporter"><svg width="22" height="24" viewBox="0 0 22 24" fill="#9a9a9a" aria-hidden="true"><circle cx="11" cy="8" r="5.5"/><path d="M0 24c0-6 5-9 11-9s11 3 11 9z"/></svg></span>
  <span class="supporter"><svg width="22" height="24" viewBox="0 0 22 24" fill="#9a9a9a" aria-hidden="true"><circle cx="11" cy="8" r="5.5"/><path d="M0 24c0-6 5-9 11-9s11 3 11 9z"/></svg></span>
  <span class="supporter"><svg width="22" height="24" viewBox="0 0 22 24" fill="#9a9a9a" aria-hidden="true"><circle cx="11" cy="8" r="5.5"/><path d="M0 24c0-6 5-9 11-9s11 3 11 9z"/></svg></span>
</div>
<div class="rule abs" style="top:307px"></div>
<div class="support-now abs">My Support is now : $5 / month</div>

<svg class="progress-ring abs" width="156" height="156" viewBox="0 0 156 156" aria-hidden="true">
  <circle cx="78" cy="78" r="74" fill="none" stroke="var(--brand)" stroke-width="5"/>
  <circle cx="78" cy="78" r="74" fill="none" stroke="var(--ring-rest)" stroke-width="5"
          stroke-dasharray="256 465" transform="rotate(-90 78 78)"/>
</svg>
<div class="progress-value abs">45%</div>
<div class="given abs">$15 given</div>
<div class="needed abs">of total $35 needed</div>
<div class="per-month abs">
  <svg width="17" height="17" viewBox="0 0 17 17" fill="var(--brand)" aria-hidden="true"><path d="M1 3h15v13H1zM2.5 7v7.5h12V7z"/><rect x="4" y="1" width="2" height="4"/><rect x="11" y="1" width="2" height="4"/><rect x="4" y="9" width="2" height="2"/><rect x="7.5" y="9" width="2" height="2"/><rect x="11" y="9" width="2" height="2"/><rect x="4" y="12" width="2" height="2"/><rect x="7.5" y="12" width="2" height="2"/></svg>
  Per month need
</div>

<div class="section-label abs" style="top:553px">Participate</div>
<div class="rule abs" style="top:586px"></div>

<div class="option abs" style="top:609px"><span class="box"></span><span class="label">I am in, $1 / month</span>
  <svg width="16" height="14" viewBox="0 0 16 14" fill="#6b6b6b" aria-hidden="true"><path d="M0 0h3l.6 2H16l-2 6H5l.5 1.5H14V11H4.5L2 1.5H0z"/><circle cx="6" cy="12.5" r="1.5"/><circle cx="13" cy="12.5" r="1.5"/></svg></div>
<div class="option abs" style="top:657px"><span class="box"></span><span class="label">Oncreased, $5 / month</span>
  <svg width="16" height="14" viewBox="0 0 16 14" fill="#6b6b6b" aria-hidden="true"><path d="M0 0h3l.6 2H16l-2 6H5l.5 1.5H14V11H4.5L2 1.5H0z"/><circle cx="6" cy="12.5" r="1.5"/><circle cx="13" cy="12.5" r="1.5"/></svg></div>
<div class="option abs" style="top:705px"><span class="box"></span><span class="label">Decent help, $10 / month</span>
  <svg width="16" height="14" viewBox="0 0 16 14" fill="#6b6b6b" aria-hidden="true"><path d="M0 0h3l.6 2H16l-2 6H5l.5 1.5H14V11H4.5L2 1.5H0z"/><circle cx="6" cy="12.5" r="1.5"/><circle cx="13" cy="12.5" r="1.5"/></svg></div>
<div class="option abs" style="top:753px"><span class="box"></span><span class="label">Whole kid, $35 / month</span>
  <svg width="16" height="14" viewBox="0 0 16 14" fill="#6b6b6b" aria-hidden="true"><path d="M0 0h3l.6 2H16l-2 6H5l.5 1.5H14V11H4.5L2 1.5H0z"/><circle cx="6" cy="12.5" r="1.5"/><circle cx="13" cy="12.5" r="1.5"/></svg></div>
<div class="option abs" style="top:801px"><span class="box"></span><span class="label">My Amount</span>
  <span class="amount-field">Enter Amount</span>
  <svg width="16" height="14" viewBox="0 0 16 14" fill="#6b6b6b" aria-hidden="true"><path d="M0 0h3l.6 2H16l-2 6H5l.5 1.5H14V11H4.5L2 1.5H0z"/><circle cx="6" cy="12.5" r="1.5"/><circle cx="13" cy="12.5" r="1.5"/></svg></div>

</body>
</html>
```